Vorby Loans Benefits Summary

We are looking to put our benefits information into a summary document and make it look pretty/easy to read! I put all of the information together into a document, one tab for all of our medical plans and another for dental/vision. This document is only there as a guide. I want this to be visually appealing, so feel free to get creative with the format.

Industry/Entity Type

Mortgage Lender

Colors
31b7a3
ffcf3e

Requirements
Should not have
• I don't want a copy and pasted version of the visual I sent, with our logo attached.

```html
<!DOCTYPE html>
<html lang="en">
<head>
<meta charset="utf-8">
<title>Vorby Loans Benefits Summary</title>
<link href="https://fonts.googleapis.com/css2?family=Open+Sans:wght@400;600;700&family=Carlito:wght@400;700&display=swap" rel="stylesheet">
<style>
  :root{
    --navy:#1c3a6b;
    --teal:#31b7a3;
    --teal-text:#2b8f83;
    --yellow:#ffcf3e;
    --ink:#1a1a1a;
    --page:#ffffff;
    --backdrop:#ececec;
    --rule:#222;
    --shade:#6b6b6b;
  }
  *{box-sizing:border-box;margin:0;padding:0}
  html,body{width:1200px;height:440px;overflow:hidden;background:var(--backdrop)}
  .sheet{position:absolute;top:15px;width:580px;height:410px;background:var(--page);overflow:hidden;font-family:"Carlito",Calibri,sans-serif;color:var(--ink)}
  .sheet--medical{left:12px}
  .sheet--extras{left:608px}
  .masthead{position:absolute;left:0;top:0;width:580px;height:82px}
  .brand{position:absolute;left:0;right:0;top:22px;display:flex;justify-content:center;align-items:center;gap:6px}
  .brand__mark{width:12px;height:12px;background:var(--yellow)}
  .brand__name{font-family:"Open Sans",Arial,sans-serif;font-weight:700;font-size:30px;color:var(--teal);letter-spacing:-.5px;line-height:1}
  table{border-collapse:collapse;font-size:4.3px;line-height:5.2px}
  colgroup{border:0.6px solid var(--rule)}
  th,td{padding:0 1px;vertical-align:bottom;text-align:center;font-weight:400}
  thead th{font-weight:700}
  thead tr{border-bottom:0.6px solid var(--rule)}
  td.lbl,th.lbl{text-align:left;white-space:nowrap}
  .in{padding-left:6px}
  tr.sec{border-top:0.6px solid var(--rule)}
  .medical{position:absolute;left:14px;top:96px;width:552px;table-layout:fixed;font-size:3.9px;line-height:5px}
  .medical col.c{width:48px}
  .medical col.lb{width:72px}
  .vision{position:absolute;left:14px;top:90px;width:262px;font-size:4.6px;line-height:6.1px}
  .dental{position:absolute;left:294px;top:90px;width:272px;font-size:4.6px;line-height:6.1px}
  .caption{font-weight:700;text-align:center}
  td.blk{background:var(--shade)}
  .footer{position:absolute;left:0;right:0;bottom:0;background:var(--teal);font-family:"Open Sans",Arial,sans-serif;color:#fff;font-weight:700;text-align:center;font-size:7px;line-height:9px}
  .sheet--medical .footer{top:354px;padding-top:20px}
  .sheet--extras .footer{top:331px;padding-top:19px}
  .footer p{margin-bottom:3px}
  .notice{position:absolute;left:38px;right:38px;background:var(--yellow);border-radius:14px;color:var(--teal-text);font-family:"Open Sans",Arial,sans-serif;font-weight:600;font-size:7px;line-height:8.6px;text-align:center;padding:4px 8px}
  .sheet--medical .notice{top:342px}
  .sheet--extras .notice{top:320px}
</style>
</head>
<body>

<section class="sheet sheet--medical">
  <svg class="masthead" viewBox="0 0 580 82" aria-hidden="true"><path d="M0 0H568C550 52 505 82 445 82H0Z" fill="var(--navy)"/></svg>
  <div class="brand"><span class="brand__mark"></span><span class="brand__name">Vorby Loans</span></div>

  <table class="medical">
    <colgroup><col class="lb"></colgroup>
    <colgroup><col class="c"><col class="c"></colgroup>
    <colgroup><col class="c"><col class="c"></colgroup>
    <colgroup><col class="c"><col class="c"></colgroup>
    <colgroup><col class="c"><col class="c"></colgroup>
    <colgroup><col class="c"><col class="c"></colgroup>
    <thead>
      <tr><th></th><th colspan="2">Crestline Gold PPO 2250/0%/2250 w/ HSA TradRX</th><th colspan="2">Crestline Silver PPO 3500/50%/7900 TradRX</th><th colspan="2">Crestline Gold Pathway HMO 1000/20%/5600</th><th colspan="2">Crestline Gold PPO 750/20%/5250</th><th colspan="2">Crestline Platinum PPO 250/20%/3500</th></tr>
      <tr><th></th><th>In-Network</th><th>Non-Network</th><th>In-Network</th><th>Non-Network</th><th>In-Network</th><th>Non-Network</th><th>In-Network</th><th>Non-Network</th><th>In-Network</th><th>Non-Network</th></tr>
    </thead>
    <tbody>
      <tr class="sec"><td class="lbl">Annual Deductible<br><span class="in">Single / Family</span></td><td>$2,250 / $4,500</td><td>$6,750 / $13,500</td><td>$3,500 / $7,000</td><td>$10,500 / $21,000</td><td>$1,000 / $3,000</td><td>Not covered</td><td>$750 / $2,250</td><td>$2,250 / $4,500</td><td>$250 / $750</td><td>$2,000 / $4,000</td></tr>
      <tr class="sec"><td class="lbl">Annual Out-of-Pocket Maximum<br><span class="in">Single / Family</span></td><td>$2,250 / $4,500</td><td>$7,875 / $15,750</td><td>$7,900 / $15,800</td><td>$23,700 / $47,400</td><td>$5,600 / $11,200</td><td>Not covered</td><td>$5,250 / $10,500</td><td>$15,750 / $31,500</td><td>$3,500 / $7,000</td><td>$10,500 / $21,000</td></tr>
      <tr class="sec"><td class="lbl">Office Visit<br><br><span class="in">Primary Care</span></td><td>0% coinsurance</td><td>50% coinsurance</td><td>$50/visit</td><td>50% coinsurance</td><td>$25/visit</td><td>Not covered</td><td>$20/visit for first 3, then 20% coinsurance</td><td>50% coinsurance</td><td>$15/visit</td><td>50% coinsurance</td></tr>
      <tr><td class="lbl"><br><span class="in">Specialist</span></td><td>0% coinsurance</td><td>50% coinsurance</td><td>$75/visit</td><td>50% coinsurance</td><td>$50/visit</td><td>Not covered</td><td>$20/visit for first 3, then 20% coinsurance</td><td>50% coinsurance</td><td>$25/visit</td><td>50% coinsurance</td></tr>
      <tr class="sec"><td class="lbl">Preventative Services</td><td>No charge</td><td>50% coinsurance</td><td>No charge</td><td>50% coinsurance</td><td>No charge</td><td>Not covered</td><td>No charge</td><td>50% coinsurance</td><td>No charge</td><td>50% coinsurance</td></tr>
      <tr class="sec"><td class="lbl">Diagnostic Test &amp; Imaging</td><td>0% coinsurance</td><td>50% coinsurance</td><td>50% coinsurance</td><td>50% coinsurance</td><td>20% coinsurance</td><td>Not covered</td><td>20% coinsurance</td><td>50% coinsurance</td><td>20% coinsurance</td><td>50% coinsurance</td></tr>
      <tr class="sec"><td class="lbl">Outpatient Surgery</td><td>0% coinsurance</td><td>50% coinsurance</td><td>50% coinsurance</td><td>50% coinsurance</td><td>20% coinsurance</td><td>Not covered</td><td>20% coinsurance</td><td>50% coinsurance</td><td>20% coinsurance</td><td>50% coinsurance</td></tr>
      <tr class="sec"><td class="lbl">Emergency<br><span class="in">Emergency Room</span></td><td>0% coinsurance</td><td>Covered as In-Network</td><td>$500/visit</td><td>Covered as In-Network</td><td>$300/visit</td><td>Not covered</td><td>$300/visit</td><td>Covered as In-Network</td><td>$300/visit</td><td>Covered as In-Network</td></tr>
      <tr><td class="lbl in">Emergency Medical Transportation</td><td>0% coinsurance</td><td>Covered as In-Network</td><td>50% coinsurance</td><td>Covered as In-Network</td><td>20% coinsurance</td><td>Not covered</td><td>$300/trip</td><td>Covered as In-Network</td><td>20% coinsurance</td><td>Covered as In-Network</td></tr>
      <tr><td class="lbl in">Urgent Care</td><td>0% coinsurance</td><td>50% coinsurance</td><td>$75/visit</td><td>50% coinsurance</td><td>$50/visit</td><td>Not covered</td><td>20% coinsurance</td><td>50% coinsurance</td><td>$25/visit</td><td>50% coinsurance</td></tr>
      <tr class="sec"><td class="lbl">Hospital Stay</td><td>0% coinsurance</td><td>50% coinsurance</td><td>50% coinsurance</td><td>50% coinsurance</td><td>20% coinsurance</td><td>Not covered</td><td>20% coinsurance</td><td>50% coinsurance</td><td>20% coinsurance</td><td>50% coinsurance</td></tr>
      <tr class="sec"><td class="lbl">Mental Health/Behavioral<br>Health/Substance Abuse Services<br><br><br><span class="in">Outpatient Services</span><br><br></td><td><b>Office Visit</b><br>0% coinsurance<br><b>Other Outpatient</b><br>0% coinsurance</td><td><b>Office Visit</b><br>50% coinsurance<br><b>Other Outpatient</b><br>50% coinsurance</td><td><b>Office Visit</b><br>$50/visit<br><b>Other Outpatient</b><br>50% coinsurance</td><td><b>Office Visit</b><br>50% coinsurance<br><b>Other Outpatient</b><br>50% coinsurance</td><td><b>Office Visit</b><br>$25/visit<br><b>Other Outpatient</b><br>20% coinsurance</td><td>Not covered</td><td><b>Office Visit</b><br>$20/visit for first 3, then 20% coinsurance<br><b>Other Outpatient</b><br>20% coinsurance</td><td><b>Office Visit</b><br>50% coinsurance<br><b>Other Outpatient</b><br>50% coinsurance</td><td><b>Office Visit</b><br>$15/visit<br><b>Other Outpatient</b><br>20% coinsurance</td><td><b>Office Visit</b><br>50% coinsurance<br><b>Other Outpatient</b><br>50% coinsurance</td></tr>
      <tr><td class="lbl in">Inpatient Services</td><td>0% coinsurance</td><td>50% coinsurance</td><td>50% coinsurance</td><td>50% coinsurance</td><td>20% coinsurance</td><td>Not covered</td><td>20% coinsurance</td><td>50% coinsurance</td><td>20% coinsurance</td><td>50% coinsurance</td></tr>
      <tr class="sec"><td class="lbl">Pregnancy<br><span class="in">Office visits, childbirth/delivery</span><br><span class="in">professional &amp; facility services</span></td><td>0% coinsurance</td><td>50% coinsurance</td><td>50% coinsurance</td><td>50% coinsurance</td><td>20% coinsurance</td><td>Not covered</td><td>20% coinsurance</td><td>50% coinsurance</td><td>20% coinsurance</td><td>50% coinsurance</td></tr>
      <tr class="sec"><td class="lbl">Monthly Cost (Varies by Age)*<br>Age 30<br><span class="in">Employee</span><br><span class="in">Per Child Cost**</span><br><span class="in">Spouse/Domestic Partner Cost</span></td><td colspan="2">$134<br>$181<br>$268</td><td colspan="2">$111<br>$150<br>$222</td><td colspan="2">$114<br>$155<br>$229</td><td colspan="2">$136<br>$184<br>$273</td><td colspan="2">$149<br>$201<br>$299</td></tr>
      <tr><td class="lbl">Age 50<br><span class="in">Employee</span><br><span class="in">Per Child Cost**</span><br><span class="in">Spouse/Domestic Partner Cost</span></td><td colspan="2">$211<br>$181<br>$422</td><td colspan="2">$175<br>$150<br>$350</td><td colspan="2">$180<br>$155<br>$361</td><td colspan="2">$215<br>$184<br>$431</td><td colspan="2">$235<br>$201<br>$471</td></tr>
    </tbody>
  </table>

  <div class="footer">
    <p>*For the purpose of this document, we assume that your spouse is the same age as you and that your children are 18 years old or less.<br>Your quoted price will change based on the actual age of your spouse and children.</p>
    <p>**Children beyond the first three are covered at no additional cost.</p>
  </div>
  <div class="notice">Limitations, exceptions and other important information are provided in the summary of benefits and coverage for each plan.<br>In the event that the information in this summary differs from the plan description, the plan description will prevail.</div>
</section>

<section class="sheet sheet--extras">
  <svg class="masthead" viewBox="0 0 580 82" aria-hidden="true"><path d="M0 0H568C550 52 505 82 445 82H0Z" fill="var(--navy)"/></svg>
  <div class="brand"><span class="brand__mark"></span><span class="brand__name">Vorby Loans</span></div>

  <table class="vision">
    <caption class="caption">Vision</caption>
    <colgroup><col style="width:96px"></colgroup>
    <colgroup><col style="width:83px"><col style="width:83px"></colgroup>
    <thead><tr><th></th><th>In-Network</th><th>Non-Network</th></tr></thead>
    <tbody>
      <tr class="sec"><td class="lbl">Co-Pay<br><span class="in">First Service Provided</span><br><span class="in">Exams</span><br><br><span class="in">Materials</span></td><td colspan="2"><br>Not applicable<br>Exams $10.00<br>$25<br>Waived for conventional &amp; planned replacement contact lenses</td></tr>
      <tr class="sec"><td class="lbl">How Often Can I Obtain Service?*<br><span class="in">Exams</span><br><span class="in">Lenses</span><br><span class="in">Frames</span><br><span class="in">Materials</span></td><td colspan="2">Once/year<br>Once/year<br>Once every other year<br>Once/year</td></tr>
      <tr class="sec"><td class="lbl">Eye Exams</td><td>Copay applies</td><td>Amount over $39</td></tr>
      <tr class="sec"><td class="lbl">Lenses<br><span class="in">Single Vision</span><br><span class="in">Lined Bifocal</span><br><span class="in">Lined Trifocal</span><br><span class="in">Lenticular</span></td><td>Copay applies<br>Copay applies<br>Copay applies<br>Copay applies</td><td>Amount over $23<br>Amount over $37<br>Amount over $49<br>Amount over $64</td></tr>
      <tr class="sec"><td class="lbl">Contact Lenses<br><span class="in">Conventional</span><br><span class="in">Planned Replacement &amp; Disposable</span><br><span class="in">Medically Necessary</span><br><span class="in">Evaulation &amp; Fitting</span></td><td>Amount over $130<br>Amount over $130<br>Copay applies<br>15% off professional fee</td><td>Amount over $100<br>Amount over $100<br>Amount over $210<br>Not covered</td></tr>
      <tr class="sec"><td class="lbl">Frames</td><td>$130, 20% discount on amount over $130</td><td>Amount over $46</td></tr>
      <tr class="sec"><td class="lbl">Lens &amp; Frame Allowance</td><td>No discounts</td><td>No discounts</td></tr>
      <tr class="sec"><td class="lbl">Cosmetic Extras</td><td>Discounted at average 20%-25% off providers UCR</td><td>No discounts</td></tr>
      <tr class="sec"><td class="lbl">Laser Correction Surgery</td><td>Average 15% discount off usual price or 5% off promotional price</td><td>No discounts</td></tr>
      <tr class="sec"><td class="lbl">Monthly Cost**<br><span class="in">Employee</span><br><span class="in">Child Cost***</span><br><span class="in">Spouse/Domestic Partner Cost</span></td><td colspan="2">$9<br>$7<br>$6</td></tr>
    </tbody>
  </table>

  <table class="dental">
    <caption class="caption">Dental</caption>
    <colgroup><col style="width:88px"></colgroup>
    <colgroup><col style="width:42px"><col style="width:42px"></colgroup>
    <colgroup><col style="width:50px"><col style="width:50px"></colgroup>
    <thead>
      <tr><th></th><th colspan="2">Calendar Year Deductible</th><th colspan="2">Coinsurance (Policy Pays)</th></tr>
      <tr><th></th><th>In-Network</th><th>Non-Network</th><th>In-Network</th><th>Non-Network</th></tr>
    </thead>
    <tbody>
      <tr><td class="lbl">Preventative</td><td>$0</td><td>$0</td><td>100%</td><td>100%</td></tr>
      <tr class="sec"><td class="lbl">Basic</td><td>$50</td><td>$50</td><td>80%</td><td>80%</td></tr>
      <tr class="sec"><td class="lbl">Major</td><td>$50</td><td>$50</td><td>50%</td><td>50%</td></tr>
      <tr class="sec"><td class="lbl" style="vertical-align:middle"><br>Combined Family Deductible<br><br></td><td colspan="4" style="text-align:left;vertical-align:middle">Max deductible 3 times the per person deductible amount. Deductibles for basic and major procedures are combined for in-network and non-network.</td></tr>
      <tr class="sec"><td class="lbl" style="vertical-align:middle">Combined Maximum</td><td colspan="4" style="text-align:left">Maximums for preventative, basic, and major procedures combined. In-network and non-network maximums are $1,000 per person.</td></tr>
      <tr class="sec"><td></td><td colspan="4"><b>Orthodontia - Child</b></td></tr>
      <tr class="sec"><td></td><td><b>In-Network</b></td><td><b>Non-Network</b></td><td><b>In-Network</b></td><td><b>Non-Network</b></td></tr>
      <tr class="sec"><td class="lbl">Lifetime Deductible</td><td>$0</td><td>$0</td><td>50%</td><td>50%</td></tr>
      <tr><td class="lbl">Lifetime Maximum</td><td>$1,000</td><td>$1,000</td><td class="blk"></td><td class="blk"></td></tr>
      <tr class="sec"><td class="lbl">Monthly Cost**<br><span class="in">Employee</span><br><span class="in">Child Cost***</span><br><span class="in">Spouse/Domestic Partner Cost</span></td><td colspan="4">$40<br>$68<br>$41</td></tr>
    </tbody>
  </table>

  <div class="footer">
    <p>*Members will receive 20% off unlimited additional pairs of prescription glasses and non prescription sunglasses valid through any ClearSight doctor<br>within 12 months of the last covered exam.</p>
    <p>**For the purpose of this document, we assume that your spouse is the same age as you and that your children are 18 years old or less.<br>Your quoted price may change based on the actual age of your spouse and children.</p>
    <p>***Children beyond the first child are covered at no additional cost.</p>
  </div>
  <div class="notice">Limitations, exceptions and other important information are provided in the summary of benefits and coverage for each plan.<br>In the event that the information in this summary differs from the plan description, the plan description will prevail</div>
</section>

</body>
</html>
```